Marlo Tidecrest SUP Boards

We are a 100% owned and operated Australian Stand Up Paddle Board company, specialising in online sales of Stand Up Paddle Board packages.

We want our website to have an ocean, sunset, beach warm feel.

We sell 4 packages and need to be able to edit content and upload a number of photos of each package for sale.

Customers will be able to email us to receive quotes on freight costs and then pay via CoinLark only. We will have a Chatterbox page and Swapnest adds that need to be linked to the website also.

Target Market(s)

Surfers and Stand up paddle boarders

Industry/Entity Type

It Company

Number of Pages Required

3 page

Requirements
Must have
• Link to CoinLark for payment
• Link to Chatterbox page
• Three tabs- Welcome page, SUP Boards and a Contact us page

```html
<!DOCTYPE html>
<html lang="en">
<head>
<meta charset="utf-8">
<title>Marlo Tidecrest SUP Boards</title>
<link rel="stylesheet" href="https://fonts.googleapis.com/css2?family=Roboto:wght@300;400;500;700&family=Roboto+Slab:wght@700&display=swap">
<style>
:root{
  --black:#050505;
  --orange:#f29418;
  --orange-deep:#e8761a;
  --gold:#f7b500;
  --white:#ffffff;
  --text:#2b2b2b;
  --purple:#4b1a70;
  --flame:#e9571d;
  --blue:#1d70b8;
  --amber:#f2ac1d;
  --pack-top:#f4f7fa;
  --pack-bottom:#d5e1eb;
  --footer:#606060;
  --footer-dark:#2d2e33;
  --btn-dark:#1f1f1f;
}
*{box-sizing:border-box;margin:0;padding:0}
html,body{width:1200px;height:2311px;overflow:hidden}
body{position:relative;background:var(--white);font-family:"Roboto",Arial,sans-serif;color:var(--text)}
.abs{position:absolute}

/* header */
.site-header{position:absolute;left:0;top:0;width:1200px;height:146px;background:var(--black)}
.brand{position:absolute;left:89px;top:0;width:325px;height:146px;background:radial-gradient(circle at 55% 30%,#ffd400 0%,var(--gold) 45%,var(--orange-deep) 100%);display:flex;flex-direction:column;justify-content:center;padding-left:16px}
.brand-name{font-family:"Roboto",sans-serif;font-weight:700;font-size:30px;line-height:34px;color:#151515}
.main-nav{position:absolute;left:491px;top:62px;display:flex;align-items:center}
.main-nav a{font-size:14px;color:var(--white);text-decoration:none;text-transform:uppercase;height:43px;line-height:43px;position:absolute;white-space:nowrap}
.main-nav .is-active{background:var(--white);color:#222;width:79px;text-align:center;border-radius:3px}
.search-btn{position:absolute;left:1080px;top:66px}

/* hero */
.hero{position:absolute;left:0;top:146px;width:1200px;height:606px;background:linear-gradient(180deg,#3f8fd6 0%,#7fbff0 34%,#1f5f8a 46%,#2f7fa8 56%,#cfe1e6 68%,#a47e5a 82%,#8a6647 100%)}
.hero-title{position:absolute;left:91px;top:183px;font-size:43px;font-weight:500;color:var(--white);text-shadow:0 2px 6px rgba(0,0,0,.35)}
.hero-sub{position:absolute;left:93px;top:245px;font-size:26px;color:var(--white);text-shadow:0 1px 4px rgba(0,0,0,.35)}
.btn-start{position:absolute;left:91px;top:301px;width:149px;height:46px;border-radius:5px;background:linear-gradient(#fbae3c,var(--orange-deep));color:var(--white);font-size:14px;font-weight:500;line-height:46px;text-align:center;box-shadow:0 2px 4px rgba(0,0,0,.3)}
.hero-dots{position:absolute;left:1149px;top:190px;display:flex;flex-direction:column;gap:7px}
.hero-dots span{width:10px;height:10px;border-radius:50%;background:var(--white)}
.hero-dots .on{background:var(--orange)}

/* welcome */
.welcome{position:absolute;left:0;top:752px;width:1200px;height:268px;text-align:center}
.welcome h1{position:absolute;left:0;width:1200px;top:40px;font-size:24px;font-weight:500;color:var(--orange)}
.welcome p{position:absolute;left:89px;width:1012px;top:82px;font-size:16px;line-height:27px;text-align:justify;text-align-last:center;color:#333}
.btn-dark{background:linear-gradient(#4a4a4a,var(--btn-dark));color:var(--white);border-radius:5px;text-align:center}
.welcome .btn-dark{position:absolute;left:539px;top:192px;width:122px;height:42px;line-height:42px;font-size:16px}

/* services */
.services{position:absolute;left:0;top:1020px;width:1200px;height:386px;background:linear-gradient(110deg,#4f6f79 0%,#2e4f58 40%,#3f6a74 70%,#56808a 100%)}
.services h2{position:absolute;left:0;width:1200px;top:44px;text-align:center;font-size:22px;font-weight:400;color:var(--white)}
.service-card{position:absolute;top:106px;width:244px}
.service-photo{height:149px;border:3px solid var(--white)}
.service-card h3{margin-top:19px;font-size:12.5px;font-weight:500;color:var(--white);text-transform:uppercase}
.service-card p{margin-top:6px;font-size:10.5px;line-height:16px;color:#e5edef}
.arrow{position:absolute;top:1164px}

/* packages */
.packages-title{position:absolute;left:0;width:1200px;top:1430px;text-align:center;font-size:29px;font-weight:700;color:#111}
.packages-title span{color:var(--orange)}
.package{position:absolute;background:linear-gradient(var(--pack-top),var(--pack-bottom));text-align:center}
.package-head{height:85px;color:var(--white);display:flex;flex-direction:column;justify-content:center}
.package-head .name{font-family:"Roboto Slab",serif;font-size:12px;font-weight:700}
.package-head .price{font-family:"Roboto",sans-serif;font-size:22px;font-weight:700;margin-top:4px}
.package h4{text-align:left;margin:18px 0 0 31px;font-size:16px;font-weight:700;color:#222}
.package ul{list-style:none;margin:8px 16px 0 31px;text-align:left}
.package li{font-size:12.5px;height:37px;line-height:37px;border-bottom:1px solid #cdd7df;color:#333}
.package li:last-child{border-bottom:none}
.btn-order{position:absolute;left:50%;transform:translateX(-50%);width:176px;height:43px;line-height:43px;font-family:"Roboto Slab",serif;font-weight:700;font-size:16px}
.package.featured{box-shadow:0 0 10px rgba(0,0,0,.35);z-index:2}

/* footer */
.site-footer{position:absolute;left:0;top:1964px;width:1200px;height:228px;background:var(--footer);color:var(--white)}
.footer-col{position:absolute;top:36px}
.footer-col h5{font-size:16px;font-weight:400;padding-bottom:10px;border-bottom:1px solid #8a8a8a}
.footer-col p,.footer-col li{font-size:12px;line-height:20px;color:#f0f0f0}
.footer-col ul{list-style:none;margin-top:12px}
.footer-col li{line-height:24px}
.news-date{margin-top:12px}
.read-more{text-align:right;font-size:10.5px !important}
.newsletter-form{position:absolute;left:839px;top:2107px;display:flex}
.newsletter-form .field{width:216px;height:33px;background:var(--white);color:#999;font-size:11px;line-height:33px;padding-left:8px;border-radius:3px 0 0 3px}
.newsletter-form .join{width:57px;height:33px;background:var(--orange);color:var(--white);font-size:11px;font-weight:700;line-height:33px;text-align:center;border-radius:0 3px 3px 0}
.footer-bottom{position:absolute;left:0;top:2192px;width:1200px;height:119px;background:var(--footer-dark)}
.social{position:absolute;top:50px;display:flex;gap:16px;left:102px}
.social span{width:25px;height:25px;border-radius:50%;background:#e6e6e6}
.copyright{position:absolute;right:88px;top:52px;font-size:12px;color:var(--white)}
</style>
</head>
<body>

<header class="site-header">
  <div class="brand"><span class="brand-name">Marlo Tidecrest</span><span class="brand-name">SUP Boards</span></div>
  <nav class="main-nav">
    <a class="is-active" style="left:0">Home</a>
    <a style="left:110px">About Us</a>
    <a style="left:222px">Service</a>
    <a style="left:323px">Blog</a>
    <a style="left:405px">News</a>
    <a style="left:491px">Contact</a>
  </nav>
  <svg class="search-btn" width="30" height="30" viewBox="0 0 30 30" aria-label="Search">
    <circle cx="15" cy="15" r="13.5" fill="none" stroke="#fff" stroke-width="2"/>
    <circle cx="13.5" cy="13.5" r="5" fill="none" stroke="#fff" stroke-width="2"/>
    <line x1="17" y1="17" x2="21" y2="21" stroke="#fff" stroke-width="2.4" stroke-linecap="round"/>
  </svg>
</header>

<section class="hero" role="img" aria-label="Surfer holding a yellow board on a sandy beach by the ocean">
  <h2 class="hero-title">STAND UP PADDLE BOARD</h2>
  <p class="hero-sub">Lorem Ipsum has been the industry’s standard</p>
  <div class="btn-start">GET START NOW</div>
  <div class="hero-dots"><span class="on"></span><span></span><span></span><span></span></div>
</section>

<section class="welcome">
  <h1>WELCOME TO MARLO TIDECREST</h1>
  <p>Lorem Ipsum has been the industry’s standard dummy text ever since the 1500s, when an unknown printer took a galley of type and scrambled it to make a type specimen book. It has survived not only five centuries, but also the leap into electronic typesetting, remaining essentially unchanged. It was popularised in the 1960s with the release of Letraset sheets containing Lorem Ipsum passages,</p>
  <div class="btn-dark">Read More</div>
</section>

<section class="services" role="img" aria-label="Background photo of a surfer in the sea, tinted teal">
  <h2>OUR SERVICES</h2>
  <article class="service-card" style="left:94px">
    <div class="service-photo" role="img" aria-label="Woman with surfboard on the beach" style="background:linear-gradient(135deg,#8fd0e8,#e8eef2 55%,#3aa6c2)"></div>
    <h3>Ipsum is simply dummy text</h3>
    <p>Lorem Ipsum is simply dummy text of the<br>printing and typesetting industry</p>
  </article>
  <article class="service-card" style="left:350px">
    <div class="service-photo" role="img" aria-label="Windsurfer on the sea" style="background:linear-gradient(180deg,#a9d4f0,#4a86b8 60%,#27557f)"></div>
    <h3>Ipsum is simply dummy text</h3>
    <p>Lorem Ipsum is simply dummy text of the<br>printing and typesetting industry</p>
  </article>
  <article class="service-card" style="left:605px">
    <div class="service-photo" role="img" aria-label="Couple with surfboard on the beach" style="background:linear-gradient(180deg,#9fc8e0,#d8d0c0 60%,#c9b89a)"></div>
    <h3>Ipsum is simply dummy text</h3>
    <p>Lorem Ipsum is simply dummy text of the<br>printing and typesetting industry</p>
  </article>
  <article class="service-card" style="left:863px">
    <div class="service-photo" role="img" aria-label="Woman holding a surfboard" style="background:linear-gradient(135deg,#f4f4f4,#e2d6c4 55%,#c89a5e)"></div>
    <h3>Ipsum is simply dummy text</h3>
    <p>Lorem Ipsum is simply dummy text of the<br>printing and typesetting industry</p>
  </article>
</section>
<svg class="arrow" style="left:48px" width="22" height="58" viewBox="0 0 22 58" aria-label="Previous"><polyline points="20,2 2,29 20,56" fill="none" stroke="#1c2c30" stroke-width="2"/></svg>
<svg class="arrow" style="left:1148px" width="22" height="58" viewBox="0 0 22 58" aria-label="Next"><polyline points="2,2 20,29 2,56" fill="none" stroke="#1c2c30" stroke-width="2"/></svg>

<h2 class="packages-title">OUR <span>PACKAGES</span></h2>

<article class="package" style="left:94px;top:1500px;width:254px;height:418px">
  <div class="package-head" style="background:var(--purple)"><span class="name">SIMPLY DUMMY TEXT</span><span class="price">$19.00</span></div>
  <h4>FEATURES</h4>
  <ul><li>Lorem Ipsum is simply</li><li>Ipsum is simply</li><li>Lorem Ipsum is simply</li><li>Ipsum is simply</li><li>Lorem Ipsum is simply</li></ul>
  <div class="btn-dark btn-order" style="top:350px">ORDER NOW!</div>
</article>
<article class="package" style="left:353px;top:1500px;width:246px;height:418px">
  <div class="package-head" style="background:var(--flame)"><span class="name">SIMPLY DUMMY TEXT</span><span class="price">$46.00</span></div>
  <h4>FEATURES</h4>
  <ul><li>Lorem Ipsum is simply</li><li>Ipsum is simply</li><li>Lorem Ipsum is simply</li><li>Ipsum is simply</li><li>Lorem Ipsum is simply</li></ul>
  <div class="btn-dark btn-order" style="top:350px">ORDER NOW!</div>
</article>
<article class="package featured" style="left:602px;top:1486px;width:262px;height:436px">
  <div class="package-head" style="background:var(--blue)"><span class="name">SIMPLY DUMMY TEXT</span><span class="price">$68.00</span></div>
  <h4 style="margin-top:17px">FEATURES</h4>
  <ul><li>Lorem Ipsum is simply</li><li>Ipsum is simply</li><li>Lorem Ipsum is simply</li><li>Ipsum is simply</li><li>Lorem Ipsum is simply</li></ul>
  <div class="btn-dark btn-order" style="top:359px">ORDER NOW!</div>
</article>
<article class="package" style="left:867px;top:1500px;width:247px;height:418px">
  <div class="package-head" style="background:var(--amber)"><span class="name">SIMPLY DUMMY TEXT</span><span class="price">$78.00</span></div>
  <h4>FEATURES</h4>
  <ul><li>Lorem Ipsum is simply</li><li>Ipsum is simply</li><li>Lorem Ipsum is simply</li><li>Ipsum is simply</li><li>Lorem Ipsum is simply</li></ul>
  <div class="btn-dark btn-order" style="top:350px">ORDER NOW!</div>
</article>

<footer class="site-footer">
  <div class="footer-col" style="left:91px;width:262px">
    <h5>LATEST NEWS</h5>
    <p class="news-date">27/JULY/2015</p>
    <p style="text-align:justify">Donec consectetur diam ac nibh auctor ultricies. Integer mauris lacus, consequat in luctus id, semper sed felis. Cum sociis natoque penatibus</p>
    <p class="read-more">READ MORE &nbsp;»</p>
  </div>
  <div class="footer-col" style="left:427px;top:42px;width:55px">
    <h5 style="font-size:15px">LINK</h5>
    <ul><li>About us</li><li>Services</li><li>Presentation</li><li>Clients</li></ul>
  </div>
  <div class="footer-col" style="left:576px;width:188px">
    <h5>GET IN TOUCH</h5>
    <p style="margin-top:12px">418 Harbour Crest Rd. Suite 12<br>Noosa Heads, QLD 4567</p>
    <p style="margin-top:8px">Phone 07-5512-0198</p>
    <p style="margin-top:4px">Email: mail@marlotidecrest.com.au</p>
  </div>
  <div class="footer-col" style="left:841px;width:271px">
    <h5>NEWSLETTER</h5>
    <p style="margin-top:14px">Join our mailing list to stay up to date and get notices about our new releases!</p>
  </div>
</footer>
<div class="newsletter-form"><div class="field">mail@marlotidecrest.com.au</div><div class="join">JOIN</div></div>

<div class="footer-bottom">
  <div class="social"><span aria-label="Social link"></span><span aria-label="Social link"></span><span aria-label="Chatterbox"></span></div>
  <p class="copyright">Copyright © 2015 &nbsp;All Rights Reserved</p>
</div>

</body>
</html>
```